Small environmental consultancy needs a simple but professional web design

We are a boutique environmental consultancyand contracting business located in Margaret River in the South West of Western Australia.

We have two arms
1) Consulting which offers environmental planning, management and assessment services primarily to local government and the development industry.
2) Contracting which implements on site plans and on ground works primarily involving revegetation, bush regeneration and environmental weed control.

We need a simple yet professional web design within the wordpress platform that commmunicates professionalism, experience and technical expertise without appearing too corporate.

Something like this structure appeals:
http://fernquill.net.au/environment-services/
or
http://www.tallowbrookenvironmental.com.au/index.php

(without the image gallery function)

Target Market(s)

Local Government Officers deciding on tenders;
Developers, Engineers, Town Planning consultants looking for environmental expertise

Industry/Entity Type

Business

Number of Pages Required

5+ page

Font styles to use
Sans Serif

Colors
33a6d7
9bcb3c

Requirements
Must have
• Pages required include:
• Home
• Environmental Planning and Management
• Revegetation and Regeneration Implementation (This page can mirror the Environmental Planning and Management page exactly in structure but with different text and images)
• About Us (I think that this page can be relatively simple and generic)
• Contact (I think that this page can be very simple and generic)
Nice to have
• An ability to start out basic and quicikly establish a website presence and then build in additional drop downs and pages over time.
Should not have
• It does not need a photo gallery page;
• It does not need a major amount of space dedicated to social media and blogs etc as this is not currently particularly active area for us

```html
<!DOCTYPE html>
<html lang="en">
<head>
<meta charset="utf-8">
<title>About Us – Myrtle Ecoservices</title>
<link href="https://fonts.googleapis.com/css2?family=Open+Sans:wght@400;600;700&family=Raleway:wght@600;700&family=Teko:wght@400;500&display=swap" rel="stylesheet">
<style>
  :root {
    --blue: #33a6d7;
    --blue-dark: #1f86c4;
    --green: #9bcb3c;
    --green-dark: #76a022;
    --text: #555555;
    --heading-dark: #3b3b3b;
    --footer-bg: #ececec;
    --footer-line: #d8d8d8;
    --placeholder: #c8c8c8;
    --placeholder-text: #e6e6e6;
    --brand: #7a4a1e;
    --white: #ffffff;
  }
  * { box-sizing: border-box; margin: 0; padding: 0; }
  html, body { width: 1063px; height: 1200px; overflow: hidden; }
  body { font-family: "Open Sans", sans-serif; color: var(--text); background: var(--white); }

  .site-header {
    position: relative; height: 155px;
    background: linear-gradient(180deg, #f7f9fb 0%, #e6edf3 45%, #c9d7e3 75%, #b7c8d6 100%);
  }
  .brand { position: absolute; left: 66px; top: 88px; display: flex; align-items: center; gap: 10px; }
  .brand-dot { width: 22px; height: 22px; border-radius: 50%; background: var(--green); }
  .brand-name { font-family: "Open Sans", sans-serif; font-weight: 600; font-size: 26px; color: var(--brand); }

  .header-contact { position: absolute; right: 65px; top: 34px; width: 190px; }
  .call-label { font-weight: 700; font-size: 15px; color: #111; line-height: 1; padding-left: 42px; }
  .call-number { font-weight: 700; font-size: 25px; color: var(--blue); line-height: 1.1; text-align: right; }
  .search {
    margin-top: 13px; height: 25px; background: var(--white); border-radius: 2px;
    display: flex; align-items: center; justify-content: space-between; padding: 0 7px 0 9px;
    font-size: 12px; color: #444;
  }

  .main-nav { height: 39px; background: var(--blue); border-bottom: 2px solid var(--blue-dark); }
  .main-nav ul { list-style: none; display: flex; padding-left: 70px; height: 100%; }
  .main-nav li {
    font-family: "Raleway", sans-serif; font-weight: 700; font-size: 12.5px; color: var(--white);
    text-transform: uppercase; padding: 0 19px; display: flex; align-items: center;
  }
  .main-nav li.is-active { background: var(--blue-dark); }

  .page-banner {
    height: 112px;
    background: linear-gradient(90deg, #4a3a2c 0%, #8c6a40 12%, #5d5a4c 25%, #9fb3b3 45%, #d6e2e2 58%, #7c8c86 72%, #3b3a33 88%, #2d2a24 100%);
  }

  .content { padding: 38px 65px 0; }
  .page-title { font-family: "Teko", sans-serif; font-weight: 500; font-size: 40px; color: var(--green); line-height: 1; letter-spacing: 0.5px; }
  .intro { display: flex; justify-content: space-between; margin-top: 14px; }
  .intro-text { width: 535px; }
  .content p { font-size: 11.6px; line-height: 18.8px; }
  .content p + p { margin-top: 18px; }
  .image-slot {
    width: 374px; height: 253px; margin-top: 2px; background: var(--placeholder);
    display: flex; align-items: center; justify-content: center;
    font-family: "Raleway", sans-serif; font-weight: 700; font-size: 27px; color: var(--placeholder-text);
  }
  .full-text { margin-top: 16px; }

  .site-footer {
    position: absolute; left: 0; top: 910px; width: 1063px; height: 290px;
    background: var(--footer-bg); border-top: 1px solid var(--footer-line);
  }
  .footer-heading { font-family: "Teko", sans-serif; font-weight: 400; font-size: 21px; color: var(--heading-dark); line-height: 1; text-transform: uppercase; }
  .footer-col { position: absolute; top: 28px; }
  .footer-col p, .footer-col li { font-size: 11.6px; line-height: 18px; color: #444; list-style: none; }
  .col-about { left: 65px; }
  .col-about ul { margin-top: 7px; }
  .col-web { left: 334px; }
  .col-web p { margin-top: 7px; }
  .col-contact { left: 544px; width: 453px; }
  .call-now { position: absolute; left: 64px; top: 137px; }
  .call-now .phone { display: flex; align-items: center; gap: 6px; margin-top: 4px; font-family: "Teko", sans-serif; font-weight: 500; font-size: 33px; color: var(--green); line-height: 1; }

  .contact-form { margin-top: 12px; }
  .form-row { display: flex; gap: 8px; }
  .field {
    background: var(--white); border: 1px solid #dcdcdc; height: 33px; flex: 1;
    display: flex; align-items: center; justify-content: space-between; padding: 0 8px 0 12px;
    font-size: 12.5px; color: #aaa;
  }
  .field-message { height: 65px; align-items: flex-start; padding-top: 8px; margin-top: 8px; }
  .send-button {
    margin-top: 9px; width: 139px; height: 38px; border: 0;
    background: linear-gradient(180deg, var(--green) 0%, var(--green-dark) 100%);
    font-family: "Teko", sans-serif; font-weight: 400; font-size: 20px; color: var(--white);
    text-transform: uppercase; line-height: 38px; text-align: center;
  }
  .footer-bottom {
    position: absolute; left: 65px; right: 40px; top: 245px; border-top: 1px solid var(--footer-line);
    padding-top: 12px; font-size: 11.6px; color: #444;
  }
</style>
</head>
<body>

<header class="site-header" role="img" aria-label="Soft misty blue mountain ranges background">
  <div class="brand">
    <span class="brand-dot"></span>
    <span class="brand-name">Myrtle Ecoservices</span>
  </div>
  <div class="header-contact">
    <div class="call-label">Call Us</div>
    <div class="call-number">0412 384 706</div>
    <div class="search">
      <span>Search</span>
      <svg width="14" height="14" viewBox="0 0 14 14" aria-hidden="true"><circle cx="6" cy="6" r="4.5" fill="none" stroke="#999" stroke-width="1.8"/><line x1="9.3" y1="9.3" x2="13" y2="13" stroke="#999" stroke-width="2"/></svg>
    </div>
  </div>
</header>

<nav class="main-nav">
  <ul>
    <li>Home</li>
    <li>Environmental Planning and Management</li>
    <li>Revegetation and Bush Regeneration</li>
    <li class="is-active">About Us</li>
    <li>Contact</li>
  </ul>
</nav>

<div class="page-banner" role="img" aria-label="Sunlit forest with tall tree trunks and autumn foliage"></div>

<main class="content">
  <h1 class="page-title">ABOUT US</h1>
  <div class="intro">
    <div class="intro-text">
      <p>Lorem ipsum dolor sit amet, consectetuer adipiscing elit, sed diam nonummy nibh euismod tincidunt ut laoreet dolore magna aliquam erat ullamcorper suscipit lobortis nisl ut aliquip ex ea commodo consequat. Lorem ipsum dolor sit amet, consectetuer adipiscing elit, sed diam nonummy nibh euismod tincidunt ut laoreet dolore magna aliquam erat volutpat. Ut wisi enim ad minim veniam, quis nostrud exerci tation ullamcorper suscipit lobortis nisl ut aliquip ex ea commodo consequat.Lorem ipsum dolor sit amet, consectetuer adipiscing elit, sed diam nonummy nibh euismod tincidunt ut laoreet dolore magna aliquam erat volutpat. Ut wisi enim ad minim veniam, quis nostrud exerci tation ullamcorper suscipit lobortis nisl ut aliquip ex ea commodo consequat.</p>
      <p>Lorem ipsum dolor sit amet, consectetuer adipiscing elit, sed diam nonummy nibh euismod tincidunt ut laoreet dolore magna aliquam erat volutpat. Ut wisi enim ad minim veniam, quis nostrud exerci tation ullamcorper suscipit lobortis nisl ut aliquip ex ea commodo consequat. Lorem ipsum dolor sit amet, consectetuer adipiscing elit, sed diam nonummy nibh euismod tincidunt ut laoreet dolore magna aliquam erat ullamcorper suscipit lobortis nisl ut aliquip ex ea commodo consequat.</p>
    </div>
    <div class="image-slot">IMAGES HERE</div>
  </div>
  <div class="full-text">
    <p>Lorem ipsum dolor sit amet, consectetuer adipiscing elit, sed diam nonummy nibh euismod tincidunt ut laoreet dolore magna aliquam erat ullamcorper suscipit lobortis nisl ut aliquip ex ea commodo consequat. Lorem ipsum dolor sit amet, consectetuer adipiscing elit, sed diam nonummy nibh euismod tincidunt ut laoreet dolore magna aliquam erat volutpat. Ut wisi enim ad minim veniam, quis nostrud exerci tation ullamcorper suscipit lobortis nisl ut aliquip ex ea commodo consequat.Lorem ipsum dolor sit amet, consectetuer adipiscing elit, sed diam nonummy nibh euismod tincidunt ut laoreet dolore magna aliquam erat volutpat. Ut wisi enim ad minim veniam, quis nostrud exerci tation ullamcorper suscipit lobortis nisl ut aliquip ex ea commodo consequat.</p>
    <p>Lorem ipsum dolor sit amet, consectetuer adipiscing elit, sed diam nonummy nibh euismod tincidunt ut laoreet dolore magna aliquam erat volutpat. Ut wisi enim ad minim veniam, quis nostrud exerci tation ullamcorper suscipit lobortis nisl ut aliquip ex ea commodo consequat. Lorem ipsum dolor sit amet, consectetuer adipiscing elit, sed diam nonummy nibh euismod tincidunt ut laoreet dolore magna aliquam erat ullamcorper suscipit lobortis nisl ut aliquip ex ea commodo consequat.</p>
  </div>
</main>

<footer class="site-footer">
  <div class="footer-col col-about">
    <h2 class="footer-heading">About</h2>
    <ul>
      <li>Environmental Planning and Management</li>
      <li>Revegetation and Bush Regeneration</li>
      <li>Contacts</li>
    </ul>
  </div>
  <div class="call-now">
    <h2 class="footer-heading">Call us now:</h2>
    <div class="phone">
      <svg width="20" height="20" viewBox="0 0 24 24" aria-hidden="true"><path fill="#555" d="M6.6 10.8c1.4 2.8 3.8 5.1 6.6 6.6l2.2-2.2c.3-.3.7-.4 1-.2 1.1.4 2.3.6 3.6.6.6 0 1 .4 1 1V20c0 .6-.4 1-1 1C10.6 21 3 13.4 3 4c0-.6.4-1 1-1h3.5c.6 0 1 .4 1 1 0 1.3.2 2.5.6 3.6.1.3 0 .7-.2 1l-2.3 2.2z"/></svg>
      <span>0412 384 706</span>
    </div>
  </div>
  <div class="footer-col col-web">
    <h2 class="footer-heading">Website</h2>
    <p>www.myrtleecoservices.com.au</p>
  </div>
  <div class="footer-col col-contact">
    <h2 class="footer-heading">Contact us</h2>
    <div class="contact-form">
      <div class="form-row">
        <div class="field"><span>Name</span>
          <svg width="17" height="17" viewBox="0 0 16 16" aria-hidden="true"><circle cx="8" cy="5" r="3.5" fill="#bbb"/><path d="M1 16c0-4 3-6.5 7-6.5s7 2.5 7 6.5z" fill="#bbb"/></svg>
        </div>
        <div class="field"><span>E-mail</span>
          <svg width="19" height="14" viewBox="0 0 19 14" aria-hidden="true"><rect width="19" height="14" rx="1.5" fill="#bbb"/><path d="M1 1.5l8.5 6 8.5-6" fill="none" stroke="#fff" stroke-width="1.4"/></svg>
        </div>
      </div>
      <div class="field field-message"><span>Message</span>
        <svg width="19" height="16" viewBox="0 0 19 16" aria-hidden="true"><path d="M1 1h17v10H7l-4 4v-4H1z" fill="#bbb"/><circle cx="6" cy="6" r="1.1" fill="#fff"/><circle cx="9.5" cy="6" r="1.1" fill="#fff"/><circle cx="13" cy="6" r="1.1" fill="#fff"/></svg>
      </div>
      <div class="send-button">Send message</div>
    </div>
  </div>
  <div class="footer-bottom">© 2015 Myrtle Ecoservices. All Rights Reserved.</div>
</footer>

</body>
</html>
```